Business card design for a dynamic IT consulting company

We need a business card design for a young firm, specialized in the Telecommunications/Consulting industry. The name of the company is Quindor and Partners Business Consulting Ltd. (Short name: Quindor and Partnes)
Quindor = solve read reverse, so we aim to be uncomplicated and solution-oriented. The small pipe in our logo is also related to the word solve. So we need a new business card design, which is simple, eye catching and something non traditional (I would probably prefer a square shaped design rather than a rectangle, but open for suggestions). Attached our logo.

Target Market(s)

Usually our customers are Tier1 Telecoms providers (Q-Netra, Palorix, etc) and their executives.

Industry/Entity Type

Business

Contact Information for Business Card

Name: Bence Tolnavari
Email: b.tolnavari@quindor.hu
Web: www.quindor.hu
Mobile: +36 30 518 2769
Title: Managing Director

Optional:
Company name: Quindor and Partners Ltd.
Address: 1087 Budapest, Tolvenka str. 28/C, Hungary

Font styles to use
Other font styles liked:
• helveticaneue_medium, Prime Regular are used now.

Colors

Designer to choose colors to be used in the design.

Requirements
Must have
• I would like to have a 2 sided design.
Nice to have
• I thought if we make the logo a bit bigger (without the company name), that could go to the back with the company name below. I though, if the pipe in the logo is somehow touchable on the business card, would be nice and unique.

```html
<!DOCTYPE html>
<html lang="en">
<head>
<meta charset="utf-8">
<title>Quindor and Partners – Business Card</title>
<link rel="stylesheet" href="https://fonts.googleapis.com/css2?family=Arimo:wght@400;700&display=swap">
<style>
  :root {
    --backdrop: #6e4e36;
    --card: #f3f3f3;
    --band: #5d5e61;
    --grey-line: #6a6b6e;
    --magenta: #b3268b;
    --cyan: #1a9ad6;
    --ink: #3f3f42;
    --name-ink: #5a5b5e;
    --white: #ffffff;
  }
  * { box-sizing: border-box; margin: 0; padding: 0; }
  html, body { width: 1200px; height: 960px; overflow: hidden; }
  body {
    position: relative;
    background: var(--backdrop);
    font-family: "Arimo", Arial, sans-serif;
    color: var(--ink);
  }
  .card {
    position: absolute;
    top: 305px;
    width: 343px;
    height: 343px;
    background: var(--card);
    box-shadow: 1px 2px 4px rgba(0,0,0,0.45);
  }
  .card-front { left: 200px; }
  .card-back { left: 651px; }

  .stripe {
    position: absolute;
    left: 0;
    width: 100%;
    height: 2px;
    display: flex;
  }
  .stripe span { flex: 1; }
  .stripe span:nth-child(1) { background: var(--grey-line); }
  .stripe span:nth-child(2) { background: var(--magenta); margin: 0 1px; }
  .stripe span:nth-child(3) { background: var(--cyan); }
  .stripe-top { top: 27px; }
  .stripe-bottom { top: 94px; }

  .name-band {
    position: absolute;
    top: 31px;
    left: 0;
    width: 100%;
    height: 61px;
    background: var(--band);
    color: var(--white);
    text-align: center;
    padding-top: 10px;
  }
  .person-name {
    font-size: 18px;
    font-weight: 700;
    letter-spacing: 0.2px;
    line-height: 21px;
  }
  .person-title {
    font-size: 15px;
    font-weight: 400;
    line-height: 18px;
  }

  .contact {
    position: absolute;
    top: 164px;
    width: 100%;
    text-align: center;
    font-size: 14px;
    line-height: 18px;
  }
  .address {
    position: absolute;
    top: 275px;
    width: 100%;
    text-align: center;
    font-size: 14px;
    line-height: 18px;
  }

  .brand {
    position: absolute;
    top: 190px;
    width: 100%;
    display: flex;
    justify-content: center;
    align-items: center;
    gap: 8px;
  }
  .brand-mark {
    width: 9px;
    height: 9px;
    background: var(--magenta);
  }
  .brand-name {
    font-size: 28px;
    font-weight: 400;
    color: var(--name-ink);
  }
  .back-web {
    position: absolute;
    top: 293px;
    width: 100%;
    text-align: center;
    font-size: 13px;
    letter-spacing: 8px;
    padding-left: 8px;
    color: var(--name-ink);
  }
</style>
</head>
<body>
  <section class="card card-front">
    <div class="stripe stripe-top"><span></span><span></span><span></span></div>
    <header class="name-band">
      <h1 class="person-name">BENCE TOLNAVARI</h1>
      <p class="person-title">MANAGING DIRECTOR</p>
    </header>
    <div class="stripe stripe-bottom"><span></span><span></span><span></span></div>
    <address class="contact" style="font-style:normal">
      +36 30 518 2769<br>
      b.tolnavari@quindor.hu<br>
      www.quindor.hu
    </address>
    <p class="address">
      Quindor and Partners Ltd., 1087 Budapest<br>
      Tolvenka str. 28/C, Hungary
    </p>
  </section>

  <section class="card card-back">
    <div class="brand">
      <span class="brand-mark"></span>
      <span class="brand-name">Quindor &amp; Partners</span>
    </div>
    <p class="back-web">www.quindor.hu</p>
  </section>
</body>
</html>
```